Fresh, modern, fun business card for pediatric dental practice

Need a business card for fresh, modern, fun pediatric dental practice

Clean look that matches our website's font and colors

We prefer the look of curved corners on business cards

Target Market(s)

parents (mothers) of young children, professionals, mid-high class

Industry/Entity Type

Dental

Contact Information for Business Card

Maplebrook Pediatric Dentistry
482 Quarry Lane
Suite 517
Fernhollow, ST 00000
555.555.0193
www.maplebrookkidsdental.example

Mei-Ran Tsai, DMD
Corinne Walbeck, DMD
(we are working on our email address, but we would like that on the card as well)

Font styles to use
Sans Serif

Requirements
Must have
• All info; we would also like to make cards for individual staff members
• colors from our website and color palatte, attatched
• use same font and design as website for branding
Nice to have
• clean, simple card that has a pop of color
• we would like to see a few designs with our tag line "where smiles get brighter"
• we are not sure if we want to have it on there or not
• we would like to see a few designs incorporating the ribbon graphic on our website where the word WELCOME is

```html
<!DOCTYPE html>
<html lang="en">
<head>
<meta charset="utf-8">
<title>Maplebrook Pediatric Dentistry – Business Card</title>
<link href="https://fonts.googleapis.com/css2?family=Ubuntu:wght@500&family=Raleway:wght@500&family=Lato:wght@400&display=swap" rel="stylesheet">
<style>
  :root {
    --backdrop: #1e1e1e;
    --card-white: #f4f4f4;
    --sun-yellow: #f6b826;
    --berry-pink: #c8177f;
    --ink: #333333;
    --rule: #9a9a9a;
    --white: #ffffff;
  }
  * { margin: 0; padding: 0; box-sizing: border-box; }
  html, body { width: 1200px; height: 900px; overflow: hidden; }
  body { background: var(--backdrop); position: relative; font-family: "Lato", sans-serif; }

  .card {
    position: absolute;
    top: 184px;
    width: 302px;
    height: 491px;
    border-radius: 13px;
    text-align: center;
    overflow: hidden;
  }
  .card--front { left: 298px; background: var(--card-white); }
  .card--back { left: 645px; width: 305px; background: var(--sun-yellow); }

  .line { position: absolute; left: 0; right: 0; white-space: nowrap; }

  .brand-mark {
    position: absolute; left: 50%; width: 26px; height: 26px;
    margin-left: -13px; border-radius: 50%;
  }
  .card--front .brand-mark { top: 74px; background: var(--sun-yellow); }
  .card--back .brand-mark { top: 198px; background: var(--white); }

  .brand-name { font-family: "Ubuntu", sans-serif; font-weight: 500; line-height: 1; }
  .card--front .brand-name { color: var(--sun-yellow); }
  .card--back .brand-name { color: var(--white); }

  .card--front .brand-name__main { top: 126px; font-size: 44px; letter-spacing: 0.5px; }
  .card--front .brand-name__sub { top: 177px; font-size: 21px; letter-spacing: 1.2px; }
  .card--back .brand-name__main { top: 248px; font-size: 49px; letter-spacing: 0.5px; }
  .card--back .brand-name__sub { top: 299px; font-size: 22px; letter-spacing: 1.5px; }

  .doctor { font-family: "Raleway", sans-serif; font-weight: 500; font-size: 19px; }
  .doctor--first { top: 238px; color: var(--sun-yellow); }
  .doctor--second { top: 262px; color: var(--berry-pink); }

  .divider { position: absolute; left: 54px; right: 53px; height: 1px; background: var(--rule); }
  .divider--top { top: 299px; }
  .divider--bottom { top: 392px; }

  .contact { font-size: 13.5px; color: var(--ink); }
  .contact .label { color: var(--sun-yellow); }
  .contact--phone { top: 311px; }
  .contact--email-1 { top: 329px; }
  .contact--email-2 { top: 347px; }
  .contact--web { top: 365px; color: var(--sun-yellow); }
  .contact--web .web-domain { color: var(--berry-pink); }

  .address { font-size: 14px; color: var(--ink); }
  .address--practice { top: 403px; font-size: 15px; color: var(--sun-yellow); }
  .address--street { top: 422px; }
  .address--city { top: 440px; }
</style>
</head>
<body>
  <section class="card card--front" aria-label="Business card front">
    <span class="brand-mark"></span>
    <div class="line brand-name brand-name__main">maplebrook</div>
    <div class="line brand-name brand-name__sub">pediatric dentistry</div>

    <div class="line doctor doctor--first">Mei-Ran Tsai, DMD</div>
    <div class="line doctor doctor--second">Corinne Walbeck, DMD</div>

    <div class="divider divider--top"></div>
    <div class="line contact contact--phone"><span class="label">P:</span> 555.555.0193</div>
    <div class="line contact contact--email-1"><span class="label">E:</span> Mei-ran@maplebrookkidsdental.example</div>
    <div class="line contact contact--email-2"><span class="label">E:</span> Corinne@maplebrookkidsdental.example</div>
    <div class="line contact contact--web">www.<span class="web-domain">maplebrookkidsdental</span>.example</div>
    <div class="divider divider--bottom"></div>

    <div class="line address address--practice">Maplebrook Pediatric Dentistry</div>
    <div class="line address address--street">482 Quarry Lane</div>
    <div class="line address address--city">Suite 517&nbsp; Fernhollow, ST 00000</div>
  </section>

  <section class="card card--back" aria-label="Business card back">
    <span class="brand-mark"></span>
    <div class="line brand-name brand-name__main">maplebrook</div>
    <div class="line brand-name brand-name__sub">pediatric dentistry</div>
  </section>
</body>
</html>
```